Quick Straightforward Billboard Redesign

- Design billboard sized for 10 foot' x 36' foot width live area size and please include bleeds 6" around all sides
- Exact blue color match is imperative in headline, logo, phone number bubble or wherever used. C-83 / M-45 / Y-1 / K-0-
- What I hope to illustrate is that our company offers the best porch screening in the area area, in regards to quality, expertise, durability, storms proof, but we do not build screen porches.
- Current board is attached below from previous designer, and as you can see sizing was off, white space on edges make it appear to be sized incorrectly.
- I also attached my own little mock up idea well well if it helps, favorite image, logo, headline, etc and ideas perhaps on expanding or making this better?

Thanks so much!

Target Market(s)

Drivers and passengers, Southeastern NC, are of immense new construction and high end homes.

Industry/Entity Type

Construction

Colors
0054AA
0677BA
7BADD7
CADEEF
E8F1F8

Requirements
Must have
• Blue color matching
Nice to have
• Design spins or other thoughts on my little mock up

```html
<!DOCTYPE html>
<html lang="en">
<head>
<meta charset="utf-8">
<title>Tidewater Screening Billboard</title>
<link href="https://fonts.googleapis.com/css2?family=Oswald:wght@500;600&display=swap" rel="stylesheet">
<style>
  :root {
    --backdrop: #4a4a4a;
    --brand-blue: #0054aa;
    --sea-blue: #0677ba;
    --wave-blue: #0a6cbc;
    --coast-green: #0bb14f;
    --paper: #ffffff;
    --sky: #7badd7;
    --ceiling: #e8f1f8;
    --lawn: #8fae6a;
  }
  html, body {
    margin: 0;
    width: 1200px;
    height: 1001px;
    overflow: hidden;
    background: var(--backdrop);
  }
  .billboard {
    position: absolute;
    left: 50px;
    top: 303px;
    width: 1100px;
    height: 395px;
    display: block;
  }
  .brand-name, .headline, .phone-number {
    font-family: 'Oswald', 'Arial Narrow', sans-serif;
  }
  .brand-name { font-weight: 500; fill: var(--sea-blue); font-size: 38px; }
  .headline { font-weight: 500; font-size: 82px; }
  .headline--blue { fill: var(--brand-blue); }
  .headline--green { fill: var(--coast-green); }
  .phone-number { font-weight: 500; fill: var(--paper); font-size: 64px; }
</style>
</head>
<body>
<svg class="billboard" viewBox="0 0 1234 443" xmlns="http://www.w3.org/2000/svg">
  <defs>
    <linearGradient id="porchTones" x1="0" y1="0" x2="0" y2="1">
      <stop offset="0" stop-color="#e9eef2"/>
      <stop offset="0.35" stop-color="#dfe7ee"/>
      <stop offset="0.45" stop-color="#7badd7"/>
      <stop offset="0.6" stop-color="#8fae6a"/>
      <stop offset="0.8" stop-color="#8a7c6c"/>
      <stop offset="1" stop-color="#c9c8c2"/>
    </linearGradient>
    <clipPath id="photoShape">
      <path d="M574 62 C760 40 1000 12 1234 0 L1234 443 L574 443 Z"/>
    </clipPath>
  </defs>

  <rect class="board-field" width="1234" height="443" fill="var(--paper)"/>

  <g clip-path="url(#photoShape)">
    <rect class="porch-photo" x="574" y="0" width="660" height="443" fill="url(#porchTones)"
          role="img" aria-label="Photo of a screened lakeside porch with wicker seating, ceiling fans and a potted palm"/>
  </g>

  <path class="top-swoosh" d="M565 55 C720 20 880 6 1000 0 L1030 0 C880 10 720 30 565 55 Z" fill="var(--coast-green)"/>

  <path class="wave-blue" d="M0 338 C220 318 480 340 700 392 C900 420 1080 395 1234 350 L1234 443 L0 443 Z" fill="var(--wave-blue)"/>
  <path class="wave-white" d="M0 326 C230 300 500 330 720 390 L700 392 C480 345 220 322 0 340 Z" fill="var(--paper)"/>
  <path class="wave-green" d="M0 316 C240 282 520 310 760 382 L748 386 C510 322 240 300 0 334 Z" fill="var(--coast-green)"/>

  <g class="brand">
    <rect x="74" y="62" width="44" height="36" fill="var(--sea-blue)"/>
    <text class="brand-name" x="138" y="96" textLength="296" lengthAdjust="spacingAndGlyphs">TIDEWATER SCREENING</text>
  </g>

  <text class="headline headline--blue" x="72" y="198" textLength="438" lengthAdjust="spacingAndGlyphs">Screen your Porsh</text>
  <text class="headline headline--green" x="72" y="274" textLength="428" lengthAdjust="spacingAndGlyphs">Built for the Coast</text>

  <g class="phone-bubble">
    <rect x="735" y="333" width="390" height="79" rx="39.5" fill="var(--coast-green)"/>
    <path d="M760 358 c3 -3 7 -3 9 0 l4 6 c1 2 0 4 -2 5 l-3 2 c2 5 6 9 11 11 l2 -3 c1 -2 3 -3 5 -2 l6 4 c3 2 3 6 0 9 l-3 3 c-14 2 -34 -18 -32 -32 z" fill="var(--paper)"/>
    <text class="phone-number" x="790" y="396" textLength="300" lengthAdjust="spacingAndGlyphs">910.555.0147</text>
  </g>
</svg>
</body>
</html>
```